TA BRAMLEY BUSINESS CARD DESIGN PROJECT

We need to utilize our logo that was expertly created on PixelHarbor and now need to match this with a business card design.

```html
<!DOCTYPE html>
<html lang="en">
<head>
<meta charset="UTF-8">
<title>TA BRAMLEY Business Card</title>
<link href="https://fonts.googleapis.com/css2?family=Open+Sans:wght@400;700&display=swap" rel="stylesheet">
<style>
  :root {
    --backdrop: #232323;
    --brand-blue: #155aa8;
    --card-white: #ffffff;
    --ink: #111111;
    --rule: #333333;
  }
  * { margin: 0; padding: 0; box-sizing: border-box; }
  html, body {
    width: 1200px; height: 780px; overflow: hidden;
    background: var(--backdrop);
    font-family: "Open Sans", Arial, sans-serif;
  }
  .canvas {
    width: 1200px; height: 780px;
    display: flex; align-items: center; justify-content: center; gap: 40px;
  }
  .card {
    width: 540px; height: 309px; position: relative;
    box-shadow: 0 10px 30px rgba(0,0,0,0.45);
  }
  .card--front { background: var(--card-white); display: flex; }
  .card--back {
    background: var(--brand-blue);
    display: flex; align-items: center; justify-content: center;
  }
  .brand-mark {
    display: flex; align-items: center; gap: 12px;
    font-weight: 700; letter-spacing: 0.08em; white-space: nowrap;
  }
  .brand-mark__dot { border-radius: 50%; flex-shrink: 0; }
  .card--front .brand-mark { color: var(--brand-blue); font-size: 26px; }
  .card--front .brand-mark__dot { width: 18px; height: 18px; background: var(--brand-blue); }
  .card--back .brand-mark { color: var(--card-white); font-size: 46px; }
  .card--back .brand-mark__dot { width: 30px; height: 30px; background: var(--card-white); }
  .front__logo-zone {
    width: 250px; display: flex; align-items: center; justify-content: center;
  }
  .front__divider {
    width: 1px; background: var(--rule); margin: 40px 0 50px;
  }
  .front__details {
    flex: 1; padding: 58px 0 0 28px; color: var(--ink);
  }
  .contact__name {
    color: var(--brand-blue); font-weight: 700; font-size: 24px; line-height: 1.1;
  }
  .contact__title { font-size: 14px; margin-top: 4px; }
  .contact__address { font-size: 13px; line-height: 1.4; margin-top: 10px; }
  .contact__list { list-style: none; margin-top: 8px; font-size: 13px; line-height: 1.45; }
  .contact__list li { display: flex; align-items: center; gap: 7px; }
  .contact__icon { width: 12px; height: 12px; fill: var(--brand-blue); flex-shrink: 0; }
</style>
</head>
<body>
<main class="canvas">
  <section class="card card--front" aria-label="Business card front">
    <div class="front__logo-zone">
      <div class="brand-mark"><span class="brand-mark__dot"></span>TA BRAMLEY</div>
    </div>
    <div class="front__divider"></div>
    <div class="front__details">
      <h1 class="contact__name">Lena Marsh</h1>
      <p class="contact__title">Managing Director</p>
      <p class="contact__address">480 Elmridge Ave. Suite 12<br>Dallin, TX 75010</p>
      <ul class="contact__list">
        <li>
          <svg class="contact__icon" viewBox="0 0 24 24" aria-hidden="true"><path d="M6.6 10.8a15.1 15.1 0 0 0 6.6 6.6l2.2-2.2a1 1 0 0 1 1-.25 11.4 11.4 0 0 0 3.6.57 1 1 0 0 1 1 1V20a1 1 0 0 1-1 1A17 17 0 0 1 3 4a1 1 0 0 1 1-1h3.5a1 1 0 0 1 1 1c0 1.25.2 2.45.57 3.6a1 1 0 0 1-.25 1z"/></svg>
          (555) 204-8136
        </li>
        <li>
          <svg class="contact__icon" viewBox="0 0 24 24" aria-hidden="true"><path d="M2 5h20v14H2z M4 7v.5l8 5 8-5V7l-8 5z" fill-rule="evenodd"/></svg>
          info@tabramley.com
        </li>
        <li>
          <svg class="contact__icon" viewBox="0 0 24 24" aria-hidden="true"><circle cx="12" cy="12" r="10"/><path d="M2 12h20M12 2c3 3 3 17 0 20M12 2c-3 3-3 17 0 20" stroke="#fff" stroke-width="1.4" fill="none"/></svg>
          www.tabramley.com
        </li>
      </ul>
    </div>
  </section>
  <section class="card card--back" aria-label="Business card back">
    <div class="brand-mark"><span class="brand-mark__dot"></span>TA BRAMLEY</div>
  </section>
</main>
</body>
</html>
```